Wordpress Design Project for Bankruptcy Law Office in San Francisco

our current website: www.dorvanelilaw-example.com

we would like to re-design it for wordpress to make it faster and a bit more modern.

content should be similar to what we have there right now but also we do family law

please include logo for law office:

Law Office of Marta K. Dolvenidze

Thank you.
Updates

please see attached word document with logos that we like as an example.

we do tend to like color red.  darker red.

Please submit your design variations and logo as soon as possible.   We would like to go over them and make our decision

Reason: Please create couple of more variations of logo for your design, so we can make our decision what we like the most. Please see word doc for samples: Text: Law Office Of Marta K. Dolvenidze

Reason: final touches

Target Market(s)

bankruptcy and family law clients

Industry/Entity Type

Family Law

Requirements
Must have
• see examples of law sites
http://promo.lexorbin-example.com/testimonials

- new logo: Law Office of Marta K. Dolvenidze
- client intake form
- blog
- contact us form

Nice to have
• - map
- red color
- on the front page a nice photo of SF or a happy family

```html
<!DOCTYPE html>
<html lang="en">
<head>
<meta charset="utf-8">
<title>Law Office of Marta K. Dolvenidze</title>
<link href="https://fonts.googleapis.com/css2?family=Cinzel:wght@400;500&family=PT+Sans:wght@400;700&family=Arimo:wght@400;700&family=Yanone+Kaffeesatz:wght@500&display=swap" rel="stylesheet">
<style>
:root{
  --maroon:#3d0910;
  --red:#a3111f;
  --red-dark:#6e0a14;
  --grey:#cfcfcf;
  --ink:#1a1a1a;
  --text:#2b2b2b;
  --white:#fff;
  --brown:#7a3410;
  --seal:rgba(255,255,255,.16);
}
*{margin:0;padding:0;box-sizing:border-box}
html,body{width:960px;height:1200px;overflow:hidden;background:var(--maroon)}
body{position:relative;font-family:"PT Sans",sans-serif;color:var(--text)}
.page{position:absolute;left:92px;top:16px;width:776px;height:1102px;background:var(--white)}
.masthead{position:absolute;left:0;top:0;width:776px;height:86px;background:linear-gradient(180deg,#b0141f,#7d0a15)}
.brand{position:absolute;left:20px;top:20px;display:flex;align-items:center;gap:10px;color:var(--white);font-family:"Cinzel",serif}
.brand-mark{width:20px;height:20px;background:var(--white);align-self:flex-end;margin-bottom:4px}
.brand-name{line-height:1}
.brand-name .small{display:block;font-size:16px;margin-left:70px;margin-bottom:3px}
.brand-name .big{display:block;font-size:22px;letter-spacing:.5px;border-top:1px solid rgba(255,255,255,.6);padding-top:2px}
.phone{position:absolute;right:10px;top:18px;display:flex;align-items:center;gap:6px;color:var(--white);font-family:"Cinzel",serif;font-size:21px}
.phone svg{width:20px;height:20px}
.member{position:absolute;right:10px;top:53px;height:33px;width:152px;background:#0d0d0d;border-radius:6px 6px 0 0;color:var(--white);font-family:"Arimo",sans-serif;font-size:9.5px;padding:11px 0 0 7px}
.member span{color:#ff2a2a}
.nav{position:absolute;left:-16px;top:86px;width:808px;height:36px;background:var(--grey);display:flex;align-items:center;padding-left:34px}
.nav a{font-family:"Cinzel",serif;font-weight:500;font-size:15.5px;color:var(--ink);text-decoration:none;margin-right:31px;height:36px;line-height:38px;letter-spacing:.3px}
.nav a.active{background:var(--red);color:var(--white);padding:0 19px;margin-right:14px}
.nav a:last-child{margin-right:0}
.nav-fold{position:absolute;top:122px;width:16px;height:16px}
.hero{position:absolute;left:17px;top:139px;width:746px;height:311px;background:linear-gradient(90deg,#e6dccd 0%,#e2d2bf 45%,#d9b599 70%,#cfc6b8 100%)}
.hero .rule{position:absolute;left:0;width:380px;height:1px;background:rgba(150,120,90,.35)}
.hero .tagline{position:absolute;font-family:"Yanone Kaffeesatz",sans-serif;font-size:44px;color:var(--brown);line-height:1}
.contact{position:absolute;left:14px;top:467px;width:195px;height:269px;background:var(--red);border:2px dashed #bbb}
.contact h3{color:var(--white);font-size:14px;font-weight:700;margin:10px 0 0 12px}
.contact .note{color:var(--white);font-size:10px;margin:16px 0 0 18px}
.field{position:absolute;left:11px;width:164px;height:20px;background:linear-gradient(#f2f2f2,#c9c9c9);border-radius:2px;font-size:10px;color:#222;padding:4px 7px}
.field.msg{height:56px}
.submit{position:absolute;left:120px;top:249px;width:53px;height:20px;background:#000;color:var(--white);font-size:10px;text-align:center;line-height:21px}
.about{position:absolute;left:226px;top:466px;width:530px}
.about h2{font-size:15px;font-weight:700;color:#111;margin-left:1px}
.about h2.second{margin-top:14px}
.about p{font-size:10.4px;line-height:17.6px;text-align:justify;margin-top:4px}
.about p+p{margin-top:17px}
.card{position:absolute;top:754px;width:240px;height:196px;border-radius:6px;background:linear-gradient(180deg,#d4d4d4,#f5f5f5 30%,#ffffff);box-shadow:0 8px 8px -4px rgba(0,0,0,.35)}
.card h4{font-size:21px;font-weight:400;color:#333;margin:18px 0 0 14px}
.card .photo{position:absolute;left:18px;top:45px;width:201px;height:50px;background:linear-gradient(90deg,#5a4c44,#cdb9a4,#8a7564)}
.card p{position:absolute;left:16px;top:100px;width:206px;font-family:"Arimo",sans-serif;font-size:9.4px;line-height:12.8px;text-align:justify;color:#222}
.card .more{position:absolute;right:10px;bottom:10px;font-family:"Arimo",sans-serif;font-size:9.6px;font-weight:700;color:#000}
.footer{position:absolute;left:0;top:986px;width:776px;height:116px;background:linear-gradient(180deg,#a3111f,#6a0712)}
.disclaimer{position:absolute;left:18px;top:34px;width:470px;font-family:"Arimo",sans-serif;font-size:8.8px;line-height:14.4px;color:var(--white);letter-spacing:-.2px}
.badges{position:absolute;left:508px;top:30px;display:flex;gap:14px}
.badge{width:70px;height:70px;border-radius:6px;background:var(--seal)}
.bottom{position:absolute;left:0;top:1128px;width:960px;height:30px;font-family:"Arimo",sans-serif;color:var(--white)}
.copyright{position:absolute;left:88px;top:7px;font-size:9.5px}
.follow{position:absolute;left:674px;top:9px;font-size:9.6px}
.social{position:absolute;top:3px;width:18px;height:18px;background:#8a8a8a;border-radius:2px}
.paynow{position:absolute;left:788px;top:2px;width:79px;height:19px;border-radius:3px;background:var(--red);font-size:10.5px;font-weight:700;color:var(--white);text-align:center;line-height:19px}
</style>
</head>
<body>
<div class="page">
  <header class="masthead">
    <div class="brand">
      <div class="brand-mark"></div>
      <div class="brand-name"><span class="small">LAW OFFICE OF</span><span class="big">MARTA K. DOLVENIDZE</span></div>
    </div>
    <div class="phone">
      <svg viewBox="0 0 20 20"><rect width="20" height="20" rx="3" fill="#fff"/><path d="M6 4c1 0 2 2 2 3s-1 1-1 2 2 4 3 4 1-1 2-1 3 1 3 2-1 2-2 2C8 16 4 11 4 6c0-1 1-2 2-2z" fill="#a3111f"/></svg>
      <span>415-555-0147</span>
    </div>
    <div class="member">Already a Member ? <span>Login Here</span></div>
  </header>
  <nav class="nav">
    <a class="active">HOME</a><a>ABOUT US</a><a>AREAS OF PRACTICE</a><a>RESOURCES</a><a>BLOG</a><a>FAQ</a><a>CONTACT US</a>
  </nav>
  <svg class="nav-fold" style="left:-16px" viewBox="0 0 16 16"><polygon points="0,0 16,0 16,16" fill="#888"/></svg>
  <svg class="nav-fold" style="left:776px" viewBox="0 0 16 16"><polygon points="0,0 16,0 0,16" fill="#888"/></svg>

  <section class="hero" role="img" aria-label="Open hands gently holding a golden butterfly on a soft cream background">
    <div class="rule" style="top:106px"></div>
    <div class="rule" style="top:238px"></div>
    <div class="tagline" style="left:28px;top:126px">Always Protecting</div>
    <div class="tagline" style="left:142px;top:180px">Client's Interests!</div>
  </section>

  <form class="contact">
    <h3>CONTACT FORM</h3>
    <p class="note">Fields marked with * are required.</p>
    <div class="field" style="top:68px">Name *</div>
    <div class="field" style="top:97px">Email *</div>
    <div class="field" style="top:126px">Phone</div>
    <div class="field" style="top:155px">Subject *</div>
    <div class="field msg" style="top:184px">Message *</div>
    <div class="submit">SUBMIT</div>
  </form>

  <section class="about">
    <h2>About Marta K. Dolvenidze</h2>
    <p>The Law Offices of Marta K. Dolvenidze is a consumer law office dedicated to consumer protection and zealously defending the rights of our clients. We offer the big firm quality legal representation with a small firm individualized attention to each client.</p>
    <p>Our office offers services in: all types of consumer bankruptcy filings, i.e. Chapter 7, Chapter 13, Chapter 11, negotiating a settlement of your debts, assisting you in the defense of collection litigation and defending you against foreclosure. Please review our site and see what we may be able to offer you. Feel free to call us at (415) 555-0147 or use our free case evaluation form.</p>
    <h2 class="second">Speak to a Lawyer</h2>
    <p style="margin-top:0">Unlike some other law firms, when you call the Law Office of Marta K. Dolvenidze you will speak to an actual attorney. Not a paralegal or assistant. And even after retaining our office you will still speak to an attorney unlike other firms where you cannot get a hold of your attorney after several attempts.</p>
  </section>

  <article class="card" style="left:14px">
    <h4>Heading 1</h4>
    <div class="photo" role="img" aria-label="Lawyer meeting with a couple at a table"></div>
    <p>This page is available, however, but because occasionally circumstances occur in which toil and pain can procure him some great. To take a trivial example, which of us ever undertakes laborious physical exercise, except to obtain some advantage from it.</p>
    <span class="more">read more...</span>
  </article>
  <article class="card" style="left:268px">
    <h4>Heading 2</h4>
    <div class="photo" role="img" aria-label="Happy family sitting in a car"></div>
    <p>This page is available, however, but because occasionally circumstances occur in which toil and pain can procure him some great. To take a trivial example, which of us ever undertakes laborious physical exercise, except to obtain some advantage from it.</p>
    <span class="more">read more...</span>
  </article>
  <article class="card" style="left:521px">
    <h4>Heading 3</h4>
    <div class="photo" role="img" aria-label="Smiling couple relaxing together" style="background:linear-gradient(90deg,#dfe6ee,#c7a88e,#e9eef3)"></div>
    <p>This page is available, however, but because occasionally circumstances occur in which toil and pain can procure him some great. To take a trivial example, which of us ever undertakes laborious physical exercise, except to obtain some advantage from it.</p>
    <span class="more">read more...</span>
  </article>

  <footer class="footer">
    <p class="disclaimer">Disclaimer: The Law Offices of Marta K. Dolvenidze is a Debt Relief law firm as defined by 11 U.S.C. 528. We help people file for Bankruptcy Relief under the Bankruptcy Code. The information contained on this website is not to be construed as legal advice. It is not intended to solicit or form an attorney-client relationship. We do not guarantee any result and prior results do not guarantee a similar outcome. This is an attorney advertisement and this website is for informational purposes only.</p>
    <div class="badges">
      <div class="badge" role="img" aria-label="Professional accreditation badge"></div>
      <div class="badge" role="img" aria-label="Association membership badge"></div>
      <div class="badge" role="img" aria-label="Attorney association badge"></div>
    </div>
  </footer>
</div>

<div class="bottom">
  <span class="copyright">Copyright © 2010 Marta K. Dolvenidze. All Rights Reserved.</span>
  <span class="follow">follow us on</span>
  <span class="social" style="left:733px" aria-label="Social profile"></span>
  <span class="social" style="left:759px" aria-label="Social profile"></span>
  <span class="paynow">Pay Now</span>
</div>
</body>
</html>
```